Personal training and nutrition business needs business card design

We need a business card that outlays our services and invites potential customers to join our team and take the first step to a healthier and more enjoyable life. We cater for any level of fitness and specialize in weight loss and conditioning, strength training, muscle gain and strength endurance. Whether you are just starting off or need some help getting to the next level of your journey we are here to get the job done.
We specialize in one on one or one on two personal training sessions and each program will be custom made to suit individual fitness goals of our clients

```html
<!DOCTYPE html>
<html lang="en">
<head>
<meta charset="utf-8">
<title>Stride &amp; Pulse — Business Card</title>
<link href="https://fonts.googleapis.com/css2?family=Roboto:wght@400;500;900&family=Oswald:wght@500&family=Exo+2:ital,wght@1,800&display=swap" rel="stylesheet">
<style>
  :root{
    --backdrop:#2b2b2b;
    --card:#efefef;
    --ink:#111111;
    --text:#2a2a2a;
    --violet:#5a3a8e;
    --violet-mid:#7a4a9c;
    --orchid:#a5599f;
    --white:#ffffff;
  }
  *{margin:0;padding:0;box-sizing:border-box}
  html,body{width:1200px;height:1138px;overflow:hidden;background:var(--backdrop)}
  .stage{position:relative;width:1200px;height:1138px}
  .card{position:absolute;width:622px;height:375px;border-radius:16px;background:var(--card);overflow:hidden;font-family:"Roboto",sans-serif}
  .card--front{left:274px;top:186px}
  .card--back{left:276px;top:607px;width:618px}

  /* front */
  .front-brand{position:absolute;left:0;right:0;top:80px;text-align:center}
  .brand-dot{display:block;margin:0 auto 22px;width:92px;height:92px;border-radius:50%;background:linear-gradient(135deg,var(--violet),var(--orchid))}
  .brand-name{font-family:"Roboto",sans-serif;font-weight:900;font-size:40px;letter-spacing:1px;text-transform:uppercase;color:var(--ink);line-height:1}
  .tagline{font-family:"Oswald",sans-serif;font-weight:500;font-size:12.5px;letter-spacing:1.6px;color:var(--orchid);text-transform:uppercase;margin-top:10px}
  .front-web{position:absolute;left:0;right:0;top:322px;display:flex;align-items:center;justify-content:center;gap:18px;font-size:15.5px;color:var(--ink)}
  .front-web .rule{width:70px;height:2px;background:var(--ink)}
  .front-web b{font-weight:400;color:var(--violet-mid)}
  .front-band{position:absolute;left:0;right:0;bottom:0;height:8px;background:linear-gradient(90deg,var(--orchid),var(--violet))}

  /* back */
  .back-brand{position:absolute;left:60px;top:55px;width:210px;text-align:left}
  .back-brand .brand-dot{margin:0 0 16px 48px;width:78px;height:78px}
  .back-brand .brand-name{font-size:33px;line-height:1.05}
  .back-brand .tagline{font-size:8.6px;letter-spacing:.9px;margin-top:8px}
  .holder{position:absolute;right:40px;top:50px;text-align:right}
  .holder-name{font-family:"Exo 2",sans-serif;font-style:italic;font-weight:800;font-size:25px;letter-spacing:1px;color:var(--violet);text-transform:uppercase}
  .holder-role{font-size:16px;color:var(--text);margin-top:4px}
  .address{margin-top:30px;font-size:16px;line-height:25px;color:var(--text)}
  .edge-tab{position:absolute;right:-22px;top:42px;width:40px;height:68px;border-radius:50%;background:linear-gradient(180deg,var(--violet-mid),var(--orchid))}
  .wave{position:absolute;left:0;bottom:0}
  .contacts{position:absolute;right:32px;top:277px;list-style:none;text-align:right}
  .contacts li{display:flex;align-items:center;justify-content:flex-end;gap:12px;height:24px;font-size:15.5px;color:var(--white)}
  .contacts svg{width:15px;height:15px}
</style>
</head>
<body>
<main class="stage">

  <section class="card card--front">
    <div class="front-brand">
      <span class="brand-dot"></span>
      <div class="brand-name">Stride &amp; Pulse</div>
      <div class="tagline">Personal Training.&nbsp; Nutrition. Motivation</div>
    </div>
    <div class="front-web"><span class="rule"></span><span>www.<b>stride</b>n<b>pulse</b>.com</span><span class="rule"></span></div>
    <div class="front-band"></div>
  </section>

  <section class="card card--back">
    <span class="edge-tab"></span>
    <div class="back-brand">
      <span class="brand-dot"></span>
      <div class="brand-name">Stride<br>&amp; Pulse</div>
      <div class="tagline">Personal Training.&nbsp; Nutrition. Motivation</div>
    </div>
    <div class="holder">
      <div class="holder-name">Mark Dalton</div>
      <div class="holder-role">Personal Trainer</div>
      <div class="address">4821 Cedar Ridge Lane<br>Fairview Texas 75069</div>
    </div>
    <svg class="wave" width="618" height="375" viewBox="0 0 618 375">
      <defs>
        <linearGradient id="waveFill" x1="0" y1="0" x2="1" y2="0">
          <stop offset="0" stop-color="#5a3a8e"/>
          <stop offset="1" stop-color="#a5599f"/>
        </linearGradient>
      </defs>
      <path d="M0,275 C110,320 220,350 320,300 C420,250 520,200 618,228 L618,375 L0,375 Z" fill="url(#waveFill)"/>
      <path d="M0,300 C120,335 230,360 330,312 C430,262 525,220 618,248 L618,375 L0,375 Z" fill="#efefef"/>
      <path d="M50,300 C150,340 260,352 380,300 C300,360 160,350 50,300 Z" fill="#a5599f" opacity=".7"/>
      <path d="M0,335 C120,355 240,370 340,325 C440,275 530,236 618,258 L618,375 L0,375 Z" fill="url(#waveFill)"/>
    </svg>
    <ul class="contacts">
      <li>+1 (555) 204-7731
        <svg viewBox="0 0 16 16"><path d="M3 2h3l1.5 3.5-2 1.2a9 9 0 0 0 3.8 3.8l1.2-2L14 10v3a1 1 0 0 1-1 1A11 11 0 0 1 2 3a1 1 0 0 1 1-1z" fill="#fff"/></svg></li>
      <li>www.stridenpulse.com
        <svg viewBox="0 0 16 16"><circle cx="8" cy="8" r="6.3" fill="none" stroke="#fff" stroke-width="1.4"/><ellipse cx="8" cy="8" rx="2.8" ry="6.3" fill="none" stroke="#fff" stroke-width="1.2"/><path d="M1.8 8h12.4" stroke="#fff" stroke-width="1.2"/></svg></li>
      <li>mark@stridenpulse.com
        <svg viewBox="0 0 16 16"><rect x="1.5" y="3.5" width="13" height="9" fill="none" stroke="#fff" stroke-width="1.4"/><path d="M1.5 3.5 8 9l6.5-5.5" fill="none" stroke="#fff" stroke-width="1.4"/></svg></li>
    </ul>
  </section>

</main>
</body>
</html>
```